Tamquist - digital sales and services + dropshipping shopify

Hello
I’m reaching out because I need help improving my current website setup. While I like the unique design, the desktop version feels empty and incomplete, and I’d like to enhance it to make it more engaging and effective.
**Here are the key areas I need assistance with:**
1. **Desktop Version Enhancements:**
- Add more content, visuals, and interactive elements to fill the empty spaces.
- Optimize the layout to ensure it looks engaging and consistent across devices.
2. **E-commerce Integration:**
- I need to integrate Shopify (or a similar service) for managing sales, product listings, and payments efficiently.
- Set up sales funnels and automation to streamline lead conversion and order processing.
3. **Business Focus Areas:**
- The website should reflect my business focus on sales, lead generation, AI integration, efficient business setup, middlemen services, and dropshipping.
- I want clear sections dedicated to explaining these services and showcasing how they add value.
The goal is to make the website look and feel complete, especially on desktop, and to support my business model effectively.
I will also need more logos, that builds on my original logo, for the different niches we will launch in the future.
Can you help me with these updates, and if so, could you provide an estimate on the timeline and cost?
Looking forward to working with you!
Best regards,
Gordon
https://pagenook.co/Tamquist-Shelfset/shop
Industry/Entity Type
Leadgen, ai integration, api, digital services sales, dropshipping
Coding
Coded - Design and coding required
Number of Pages Required
5+ page
Look and feel

```html
<!DOCTYPE html>
<html lang="en">
<head>
<meta charset="utf-8">
<title>Tamquist — homepage concepts</title>
<link href="https://fonts.googleapis.com/css2?family=Audiowide&family=Lato:wght@400;700&display=swap" rel="stylesheet">
<style>
:root{
  --bg:#cdcdcd;
  --green:#3fa31c;
  --green-dark:#1f6d0a;
  --lime:#e0f5cc;
  --ink:#141414;
  --dark:#1d1d1d;
  --muted:#444;
  --soft:#f4f4f4;
  --white:#ffffff;
}
*{margin:0;padding:0;box-sizing:border-box}
html,body{width:994px;height:1200px;overflow:hidden}
body{background:var(--bg);font-family:"Lato",sans-serif;color:var(--ink)}
.page{position:absolute;top:16px;width:305px;background:var(--white);overflow:hidden;box-shadow:0 0 4px rgba(0,0,0,.18)}
.page-a{left:19px}.page-b{left:343px}.page-c{left:667px}
section,footer{position:relative;overflow:hidden}
.kicker{font-family:"Audiowide",sans-serif;font-size:5px;color:var(--green);letter-spacing:.2px}
.title{font-family:"Audiowide",sans-serif;font-weight:400;font-size:11px;line-height:14px;color:var(--ink);white-space:nowrap}
.copy{font-size:3.4px;line-height:5.4px;color:var(--muted)}
.btn{display:inline-block;background:var(--green);color:var(--white);font-family:"Audiowide",sans-serif;font-size:3.4px;padding:3.4px 7px;border-radius:8px;border:.8px solid var(--green-dark);white-space:nowrap}
.photo{position:absolute;border-radius:2px}
.center{text-align:center}
.band{position:absolute;left:0;width:305px;display:block}

/* nav */
.nav{position:absolute;top:0;left:0;right:0;height:30px;display:flex;align-items:center;justify-content:space-between;padding:0 14px;z-index:4}
.links{display:flex;gap:5px;font-family:"Audiowide",sans-serif;font-size:3.1px;color:#333;white-space:nowrap}
.links .on{color:var(--green);text-decoration:underline}
.icons{display:flex;gap:3px;margin-left:6px}
.icons i{display:block;width:7px;height:7px;border:.6px solid #555;border-radius:50%}
.right{display:flex;align-items:center}
.brand{display:flex;flex-direction:column;align-items:center;gap:2px;font-family:"Audiowide",sans-serif;font-size:5.5px;color:var(--ink);letter-spacing:.6px;margin-top:8px}
.brand b{display:block;width:9px;height:9px;background:var(--green)}
.nav-dark .links,.nav-dark .brand{color:var(--white)}
.nav-dark .icons i{border-color:var(--white)}

/* hero */
.hero{height:170px;background:linear-gradient(120deg,#f6fcef 0%,#e4f6d2 65%,#d6f1bf 100%)}
.hero-copy{position:absolute;left:28px;top:52px;width:150px}
.hero-copy h1{font-family:"Audiowide",sans-serif;font-weight:400;font-size:10px;line-height:14px;margin:4px 0 8px}
.hero-shot{left:183px;top:46px;width:110px;height:100px;background:linear-gradient(160deg,#f2f2f2 0%,#d9e9cf 35%,#2a2a2a 55%,#3a1d3a 70%,#dcdcdc 85%)}
.hero-b{height:184px;background:linear-gradient(180deg,#1a1a1a,#2e2e2e 60%,#262626)}
.hero-b .hero-copy{left:0;right:0;width:auto;top:50px;text-align:center;color:var(--white)}
.hero-b .hero-copy .kicker{color:var(--white)}
.hero-b .hero-copy h1{color:var(--white);margin:4px 0 6px}
.hero-b .hero-shot{left:68px;top:110px;width:168px;height:76px;z-index:3;background:linear-gradient(90deg,#0f1430 0%,#1f3fa8 30%,#111 45%,#e8e8e8 60%,#111 75%,#1a1a1a 100%);border:1.4px solid #111}
.hero-c{height:161px}

/* about */
.about{height:160px;background:#fbfbfb}
.about-shot{left:0;top:20px;width:133px;height:106px;background:linear-gradient(170deg,#ffffff 0%,#ececec 18%,#141414 30%,#2a2a2a 48%,#d7d7d7 55%,#222 62%,#3b3b1a 80%,#1a1a1a 100%)}
.about-copy{position:absolute;left:152px;top:20px;width:128px}
.about-copy .title{margin:4px 0 6px}
.about-copy .copy{margin-bottom:4px}
.about-copy .btn{margin-top:4px}

/* services */
.services{height:168px;background:var(--dark);color:var(--white)}
.services-c{height:158px}
.services .title{color:var(--white);margin-top:4px}
.services .kicker{padding-top:20px}
.svc{position:absolute;width:72px}
.svc h3{font-family:"Lato",sans-serif;font-weight:700;font-size:3.8px;margin-bottom:2px;white-space:nowrap}
.svc p{font-size:3px;line-height:4.6px;color:#bdbdbd}
.svc-l{left:20px;text-align:right}
.svc-r{left:213px}
.dot{position:absolute;width:9px;height:9px;border-radius:50%;border:.7px solid var(--green)}
.dot.fill{background:var(--green);width:12px;height:12px}
.mark{position:absolute;left:108px;top:62px;width:90px;display:flex;flex-direction:column;align-items:center;gap:5px;font-family:"Audiowide",sans-serif;font-size:10px;color:var(--green)}
.mark b{display:block;width:26px;height:26px;background:var(--green)}

/* product */
.product{height:143px;background:radial-gradient(circle at 78% 45%,#eaf6e2 0,#ffffff 40%)}
.product-c{height:153px}
.prod-copy{position:absolute;left:52px;top:26px;width:100px}
.prod-copy .kicker{font-family:"Lato",sans-serif;font-weight:700}
.prod-copy .title{margin:2px 0 4px}
.price{display:flex;align-items:center;gap:5px;margin:9px 0 10px;font-size:6px;color:#333}
.price span{border:.7px solid var(--green);border-radius:50%;padding:4px 6px;color:var(--ink)}
.prod-shot{left:178px;top:20px;width:92px;height:92px;background:linear-gradient(150deg,#ffffff 0%,#e5e5e5 20%,#5b1d8a 35%,#b135d0 45%,#1f1f1f 55%,#ffffff 80%)}
.arrow{position:absolute;top:72px;width:14px;height:14px;border-radius:50%;background:var(--white);border:.5px solid #ccc;font-size:6px;line-height:13px;text-align:center;color:#333}
.dots{position:absolute;left:225px;top:116px;display:flex;gap:4px;align-items:center}
.dots i{display:block;width:2px;height:2px;border-radius:50%;background:#cfe6c2}
.dots i.on{width:4px;height:4px;background:var(--green)}

/* testimonials */
.reviews{height:140px;background:var(--soft)}
.reviews-c{height:142px}
.reviews .kicker{padding-top:22px}
.reviews .title{margin-top:3px}
.card{position:absolute;top:54px;width:120px;height:56px;background:var(--white);padding:6px 8px;box-shadow:0 0 3px rgba(0,0,0,.08)}
.card q{display:block;font-style:italic;font-size:3.1px;line-height:4.8px;color:#555;quotes:none}
.card .who{display:flex;align-items:center;gap:3px;margin-top:6px;font-size:3.4px;font-weight:700}
.card .who i{display:block;width:10px;height:10px;border-radius:50%;background:linear-gradient(135deg,#b9a07c,#5a4a3a)}
.card .stars{color:#e2a614;font-size:3px;display:block}
.chev{position:absolute;top:80px;font-size:11px;color:#222}

/* offer */
.offer{height:254px;background:var(--white)}
.offer .kicker{padding-top:22px}
.offer .title{margin-top:3px}
.offer-shot{left:68px;top:57px;width:168px;height:75px;background:linear-gradient(90deg,#101634 0%,#223fa3 28%,#121212 42%,#e6e6e6 58%,#151515 72%,#1c1c1c 100%);border:1.4px solid #111}
.clock{position:absolute;left:28px;top:131px;width:248px;height:64px;background:var(--white);box-shadow:0 -2px 6px rgba(0,0,0,.06);padding-top:10px;text-align:center}
.clock .kicker{padding:0}
.digits{display:flex;justify-content:center;align-items:flex-start;gap:10px;margin-top:5px}
.digits div{display:flex;flex-direction:column;align-items:center;width:34px}
.digits b{font-family:"Audiowide",sans-serif;font-weight:400;font-size:21px;line-height:22px}
.digits span{font-family:"Audiowide",sans-serif;font-size:4px;color:var(--green);text-decoration:underline;margin-top:3px}
.digits em{font-style:normal;font-family:"Audiowide",sans-serif;font-size:12px;line-height:20px}
.offer-note{position:absolute;left:40px;top:201px;width:224px;text-align:center}
.offer-btn{position:absolute;left:0;right:0;top:221px;text-align:center}

/* footer */
.foot{height:118px;background:var(--dark);color:var(--white)}
.foot-c{height:108px}
.foot-brand{position:absolute;left:28px;top:62px;display:flex;flex-direction:column;align-items:center;gap:4px;font-family:"Audiowide",sans-serif;font-size:12px;letter-spacing:1px}
.foot-brand b{display:block;width:22px;height:22px;background:var(--green)}
.fcol{position:absolute;top:53px}
.fcol h4{font-family:"Audiowide",sans-serif;font-weight:400;font-size:5px;padding-bottom:2px;border-bottom:.6px solid var(--green);display:inline-block;white-space:nowrap;margin-bottom:6px}
.fcol a{display:block;font-size:3.3px;line-height:7.5px;padding-left:2px;white-space:nowrap}
.socials{display:flex;gap:2px;padding-left:3px}
.socials i{display:block;width:6.5px;height:6.5px;border:.6px solid var(--white);border-radius:50%}
.rights{position:absolute;left:189px;top:106px;font-size:3.3px;white-space:nowrap}
.foot-c .foot-brand{top:26px;left:28px}
.foot-c .fcol{top:24px}
.foot-c .rights{top:72px}
</style>
</head>
<body>

<!-- Concept A -->
<main class="page page-a">
  <section class="hero">
    <nav class="nav">
      <div class="links"><span class="on">HOME</span><span>CONTACT US</span><span>REGISTER</span><span>ABOUT</span><span>SHOP</span></div>
      <div class="brand"><b></b>TAMQUIST</div>
      <div class="right"><div class="links"><span>REVIEWS</span><span>FAQ'S</span><span>CAREERS</span></div><div class="icons"><i></i><i></i><i></i><i></i></div></div>
    </nav>
    <div class="hero-copy">
      <div class="kicker">WELCOME TO TAMQUIST</div>
      <h1>HACKER SHEETS A MUST HAVE FOR YOUR SUPERBRAIN</h1>
      <span class="btn">SHOP NOW</span>
    </div>
    <div class="photo hero-shot" role="img" aria-label="Desk setup with monitor, keyboard and cheat-sheet desk mat"></div>
    <svg class="band" style="bottom:0" width="305" height="34" viewBox="0 0 305 34"><polygon points="0,8 152,34 0,34" fill="#fbfbfb"/><polygon points="305,8 152,34 305,34" fill="#fbfbfb"/><polygon points="0,0 152,26 305,0 305,8 152,34 0,8" fill="#3fa31c"/></svg>
  </section>
  <section class="about">
    <div class="photo about-shot" role="img" aria-label="Desktop clock display above a coding cheat-sheet desk mat"></div>
    <div class="about-copy">
      <div class="kicker">WHO WE ARE</div>
      <div class="title">ABOUT TAMQUIST</div>
      <p class="copy">At Tamquist, we value community and community building around hobbies and interests. We want to create more than just a store – we want to build a network of people who share a passion for quality and good experiences.</p>
      <p class="copy">Our business model focuses on carefully selected, high quality products. We specialize in these products to avoid competing on price with everyone else, and instead offer a genuine experience and an active community for our customers.</p>
      <span class="btn">READ MORE</span>
    </div>
  </section>
  <section class="services">
    <div class="kicker center">WHAT WE OFFER</div>
    <div class="title center">OUR SERVICES</div>
    <div class="svc svc-l" style="top:53px"><h3>SALES</h3><p>Clear sales flows that turn visits into steady orders</p></div>
    <div class="svc svc-l" style="top:83px"><h3>LEAD GENERATION</h3><p>Funnels that find and warm up the right buyers</p></div>
    <div class="svc svc-l" style="top:113px"><h3>AI INTEGRATION</h3><p>Smart tools that automate the daily busy work</p></div>
    <div class="svc svc-r" style="top:53px"><h3>EFFICIENT BUSINESS SETUP</h3><p>Stores, payments and systems set up right</p></div>
    <div class="svc svc-r" style="top:83px"><h3>MIDDLEMEN SERVICES</h3><p>We link makers and sellers for smooth trade</p></div>
    <div class="svc svc-r" style="top:113px"><h3>DROPSHIPPING</h3><p>Ship products with no stock held on hand</p></div>
    <i class="dot" style="left:106px;top:57px"></i><i class="dot fill" style="left:104px;top:84px"></i><i class="dot" style="left:106px;top:116px"></i>
    <i class="dot" style="left:199px;top:57px"></i><i class="dot" style="left:199px;top:87px"></i><i class="dot" style="left:199px;top:116px"></i>
    <div class="mark"><b></b>TAMQUIST</div>
    <svg class="band" style="bottom:0" width="305" height="34" viewBox="0 0 305 34"><polygon points="0,8 152,34 0,34" fill="#fff"/><polygon points="305,8 152,34 305,34" fill="#fff"/><polygon points="0,0 152,26 305,0 305,8 152,34 0,8" fill="#3fa31c"/></svg>
  </section>
  <section class="product">
    <span class="arrow" style="left:7px">←</span><span class="arrow" style="left:284px">→</span>
    <div class="prod-copy">
      <div class="kicker">Earbud</div>
      <div class="title">MIC &amp; HANGER</div>
      <p class="copy">Contact us if you are interested in quantity-produced executive office furniture or office modules for all your employees!</p>
      <div class="price">Only <span>$259.00</span></div>
      <span class="btn">ADD TO CART</span>
    </div>
    <div class="photo prod-shot" role="img" aria-label="RGB microphone on a boom arm stand"></div>
    <div class="dots"><i></i><i class="on"></i><i></i></div>
  </section>
  <section class="reviews">
    <div class="kicker center">CLIENT TESTIMONIALS</div>
    <div class="title center">WHAT OUR CUSTOMER SAYS</div>
    <span class="chev" style="left:11px">‹</span><span class="chev" style="left:287px">›</span>
    <div class="card" style="left:28px"><q>“ Lorem ipsum dolor sit amet, consectetur adipiscing elit, sed do eiusmod tempor incididunt ut labore et dolore magna minim veniam, quis aliqua Ut enim ad minim veniam.</q><div class="who"><i></i><div>Ada Renn<span class="stars">★★★★★</span></div></div></div>
    <div class="card" style="left:157px"><q>“ Lorem ipsum dolor sit amet, consectetur adipiscing elit, sed do eiusmod tempor incididunt ut labore et dolore magna minim veniam, quis aliqua Ut enim ad minim veniam.</q><div class="who"><i></i><div>Lio Marsh<span class="stars">★★★★★</span></div></div></div>
  </section>
  <section class="offer">
    <div class="kicker center">NEW OFFER</div>
    <div class="title center">GET 20% OFFER</div>
    <div class="photo offer-shot" role="img" aria-label="Shortcut cheat-sheet desk mat with keyboard and mouse"></div>
    <div class="clock"><div class="kicker">SALE END IN</div>
      <div class="digits"><div><b>01</b><span>DAYS</span></div><em>:</em><div><b>23</b><span>HOURS</span></div><em>:</em><div><b>39</b><span>MINS</span></div><em>:</em><div><b>46</b><span>SECS</span></div></div></div>
    <p class="copy offer-note">We also sell complete Gridwell Sheets packages for a professional, stylish, clear and efficient spreadsheet for whatever financial tasks you may have! This makes the journey to a more profitable economy easier!</p>
    <div class="offer-btn"><span class="btn">SHOP NOW</span></div>
  </section>
  <footer class="foot">
    <svg class="band" style="top:0" width="305" height="34" viewBox="0 0 305 34"><polygon points="0,0 305,0 305,26 152,2 0,26" fill="#fff"/><polygon points="0,26 152,2 305,26 305,32 152,8 0,32" fill="#3fa31c"/></svg>
    <div class="foot-brand"><b></b>TAMQUIST</div>
    <div class="fcol" style="left:107px"><h4>QUICK LINKS</h4><a>Home</a><a>About Us</a><a>Our Services</a><a>Products</a><a>Contact Us</a></div>
    <div class="fcol" style="left:169px"><h4>HELP LINKS</h4><a>Privacy policy</a><a>Terms of use</a><a>Sitemap</a></div>
    <div class="fcol" style="left:227px"><h4>SOCIAL MEDIA</h4><div class="socials"><i></i><i></i><i></i><i></i><i></i></div></div>
    <div class="rights">Copyright © 2024 Tamquist . All rights reserved.</div>
  </footer>
</main>

<!-- Concept B -->
<main class="page page-b">
  <section class="hero hero-b">
    <nav class="nav nav-dark">
      <div class="links"><span class="on" style="color:#fff">HOME</span><span>CONTACT US</span><span>REGISTER</span><span>ABOUT</span><span>SHOP</span></div>
      <div class="brand"><b></b>TAMQUIST</div>
      <div class="right"><div class="links"><span>REVIEWS</span><span>FAQ'S</span><span>CAREERS</span></div><div class="icons"><i></i><i></i><i></i><i></i></div></div>
    </nav>
    <div class="hero-copy">
      <div class="kicker">WELCOME TO TAMQUIST</div>
      <h1>HACKER SHEETS A MUST HAVE FOR<br>YOUR SUPERBRAIN</h1>
      <span class="btn">SHOP NOW</span>
    </div>
    <div class="photo hero-shot" role="img" aria-label="Shortcut cheat-sheet desk mat with keyboard and mouse"></div>
    <svg class="band" style="bottom:0" width="305" height="40" viewBox="0 0 305 40"><polygon points="0,8 152,40 0,40" fill="#fbfbfb"/><polygon points="305,8 152,40 305,40" fill="#fbfbfb"/><polygon points="0,0 152,32 305,0 305,8 152,40 0,8" fill="#3fa31c"/></svg>
  </section>
  <section class="about">
    <div class="photo about-shot" role="img" aria-label="Desktop clock display above a coding cheat-sheet desk mat"></div>
    <div class="about-copy">
      <div class="kicker">WHO WE ARE</div>
      <div class="title">ABOUT TAMQUIST</div>
      <p class="copy">At Tamquist, we value community and community building around hobbies and interests. We want to create more than just a store – we want to build a network of people who share a passion for quality and good experiences.</p>
      <p class="copy">Our business model focuses on carefully selected, high quality products. We specialize in these products to avoid competing on price with everyone else, and instead offer a genuine experience and an active community for our customers.</p>
      <span class="btn">READ MORE</span>
    </div>
  </section>
  <section class="services">
    <div class="kicker center">WHAT WE OFFER</div>
    <div class="title center">OUR SERVICES</div>
    <div class="svc svc-l" style="top:53px"><h3>SALES</h3><p>Clear sales flows that turn visits into steady orders</p></div>
    <div class="svc svc-l" style="top:83px"><h3>LEAD GENERATION</h3><p>Funnels that find and warm up the right buyers</p></div>
    <div class="svc svc-l" style="top:113px"><h3>AI INTEGRATION</h3><p>Smart tools that automate the daily busy work</p></div>
    <div class="svc svc-r" style="top:53px"><h3>EFFICIENT BUSINESS SETUP</h3><p>Stores, payments and systems set up right</p></div>
    <div class="svc svc-r" style="top:83px"><h3>MIDDLEMEN SERVICES</h3><p>We link makers and sellers for smooth trade</p></div>
    <div class="svc svc-r" style="top:113px"><h3>DROPSHIPPING</h3><p>Ship products with no stock held on hand</p></div>
    <i class="dot" style="left:106px;top:57px"></i><i class="dot fill" style="left:104px;top:84px"></i><i class="dot" style="left:106px;top:116px"></i>
    <i class="dot" style="left:199px;top:57px"></i><i class="dot" style="left:199px;top:87px"></i><i class="dot" style="left:199px;top:116px"></i>
    <div class="mark"><b></b>TAMQUIST</div>
    <svg class="band" style="bottom:0" width="305" height="34" viewBox="0 0 305 34"><polygon points="0,8 152,34 0,34" fill="#fff"/><polygon points="305,8 152,34 305,34" fill="#fff"/><polygon points="0,0 152,26 305,0 305,8 152,34 0,8" fill="#3fa31c"/></svg>
  </section>
  <section class="product">
    <span class="arrow" style="left:7px">←</span><span class="arrow" style="left:284px">→</span>
    <div class="prod-copy">
      <div class="kicker">Earbud</div>
      <div class="title">MIC &amp; HANGER</div>
      <p class="copy">Contact us if you are interested in quantity-produced executive office furniture or office modules for all your employees!</p>
      <div class="price">Only <span>$259.00</span></div>
      <span class="btn">ADD TO CART</span>
    </div>
    <div class="photo prod-shot" role="img" aria-label="RGB microphone on a boom arm stand"></div>
    <div class="dots"><i></i><i class="on"></i><i></i></div>
  </section>
  <section class="reviews">
    <div class="kicker center">CLIENT TESTIMONIALS</div>
    <div class="title center">WHAT OUR CUSTOMER SAYS</div>
    <span class="chev" style="left:11px">‹</span><span class="chev" style="left:287px">›</span>
    <div class="card" style="left:28px"><q>“ Lorem ipsum dolor sit amet, consectetur adipiscing elit, sed do eiusmod tempor incididunt ut labore et dolore magna minim veniam, quis aliqua Ut enim ad minim veniam.</q><div class="who"><i></i><div>Ada Renn<span class="stars">★★★★★</span></div></div></div>
    <div class="card" style="left:157px"><q>“ Lorem ipsum dolor sit amet, consectetur adipiscing elit, sed do eiusmod tempor incididunt ut labore et dolore magna minim veniam, quis aliqua Ut enim ad minim veniam.</q><div class="who"><i></i><div>Lio Marsh<span class="stars">★★★★★</span></div></div></div>
  </section>
  <section class="offer">
    <div class="kicker center">NEW OFFER</div>
    <div class="title center">GET 20% OFFER</div>
    <div class="photo offer-shot" role="img" aria-label="Shortcut cheat-sheet desk mat with keyboard and mouse"></div>
    <div class="clock"><div class="kicker">SALE END IN</div>
      <div class="digits"><div><b>01</b><span>DAYS</span></div><em>:</em><div><b>23</b><span>HOURS</span></div><em>:</em><div><b>39</b><span>MINS</span></div><em>:</em><div><b>46</b><span>SECS</span></div></div></div>
    <p class="copy offer-note">We also sell complete Gridwell Sheets packages for a professional, stylish, clear and efficient spreadsheet for whatever financial tasks you may have! This makes the journey to a more profitable economy easier!</p>
    <div class="offer-btn"><span class="btn">SHOP NOW</span></div>
  </section>
  <footer class="foot">
    <svg class="band" style="top:0" width="305" height="34" viewBox="0 0 305 34"><polygon points="0,0 305,0 305,26 152,2 0,26" fill="#fff"/><polygon points="0,26 152,2 305,26 305,32 152,8 0,32" fill="#3fa31c"/></svg>
    <div class="foot-brand"><b></b>TAMQUIST</div>
    <div class="fcol" style="left:107px"><h4>QUICK LINKS</h4><a>Home</a><a>About Us</a><a>Our Services</a><a>Products</a><a>Contact Us</a></div>
    <div class="fcol" style="left:169px"><h4>HELP LINKS</h4><a>Privacy policy</a><a>Terms of use</a><a>Sitemap</a></div>
    <div class="fcol" style="left:227px"><h4>SOCIAL MEDIA</h4><div class="socials"><i></i><i></i><i></i><i></i><i></i></div></div>
    <div class="rights">Copyright © 2024 Tamquist . All rights reserved.</div>
  </footer>
</main>

<!-- Concept C -->
<main class="page page-c">
  <section class="hero hero-c">
    <nav class="nav">
      <div class="brand" style="margin-top:6px"><b></b>TAMQUIST</div>
      <div class="right"><div class="links"><span class="on">HOME</span><span>CONTACT US</span><span>REGISTER</span><span>ABOUT</span><span>SHOP</span><span>REVIEWS</span><span>FAQ'S</span><span>CAREERS</span></div><div class="icons"><i></i><i></i><i></i><i></i></div></div>
    </nav>
    <div class="hero-copy" style="top:55px">
      <div class="kicker">WELCOME TO TAMQUIST</div>
      <h1>HACKER SHEETS A MUST HAVE FOR YOUR SUPERBRAIN</h1>
      <span class="btn">SHOP NOW</span>
    </div>
    <div class="photo hero-shot" style="top:48px" role="img" aria-label="Desk setup with monitor, keyboard and cheat-sheet desk mat"></div>
  </section>
  <section class="about">
    <div class="photo about-shot" role="img" aria-label="Desktop clock display above a coding cheat-sheet desk mat"></div>
    <div class="about-copy">
      <div class="kicker">WHO WE ARE</div>
      <div class="title">ABOUT TAMQUIST</div>
      <p class="copy">At Tamquist, we value community and community building around hobbies and interests. We want to create more than just a store – we want to build a network of people who share a passion for quality and good experiences.</p>
      <p class="copy">Our business model focuses on carefully selected, high quality products. We specialize in these products to avoid competing on price with everyone else, and instead offer a genuine experience and an active community for our customers.</p>
      <span class="btn">READ MORE</span>
    </div>
  </section>
  <section class="services services-c">
    <div class="kicker center">WHAT WE OFFER</div>
    <div class="title center">OUR SERVICES</div>
    <div class="svc svc-l" style="top:53px"><h3>SALES</h3><p>Clear sales flows that turn visits into steady orders</p></div>
    <div class="svc svc-l" style="top:83px"><h3>LEAD GENERATION</h3><p>Funnels that find and warm up the right buyers</p></div>
    <div class="svc svc-l" style="top:113px"><h3>AI INTEGRATION</h3><p>Smart tools that automate the daily busy work</p></div>
    <div class="svc svc-r" style="top:53px"><h3>EFFICIENT BUSINESS SETUP</h3><p>Stores, payments and systems set up right</p></div>
    <div class="svc svc-r" style="top:83px"><h3>MIDDLEMEN SERVICES</h3><p>We link makers and sellers for smooth trade</p></div>
    <div class="svc svc-r" style="top:113px"><h3>DROPSHIPPING</h3><p>Ship products with no stock held on hand</p></div>
    <i class="dot" style="left:106px;top:57px"></i><i class="dot fill" style="left:104px;top:84px"></i><i class="dot" style="left:106px;top:116px"></i>
    <i class="dot" style="left:199px;top:57px"></i><i class="dot" style="left:199px;top:87px"></i><i class="dot" style="left:199px;top:116px"></i>
    <div class="mark"><b></b>TAMQUIST</div>
  </section>
  <section class="product product-c">
    <span class="arrow" style="left:7px;top:78px">←</span><span class="arrow" style="left:284px;top:78px">→</span>
    <div class="prod-copy" style="top:35px">
      <div class="kicker">Earbud</div>
      <div class="title">MIC &amp; HANGER</div>
      <p class="copy">Contact us if you are interested in quantity-produced executive office furniture or office modules for all your employees!</p>
      <div class="price">Only <span>$259.00</span></div>
      <span class="btn">ADD TO CART</span>
    </div>
    <div class="photo prod-shot" style="top:30px" role="img" aria-label="RGB microphone on a boom arm stand"></div>
    <div class="dots" style="top:125px"><i></i><i class="on"></i><i></i></div>
  </section>
  <section class="reviews reviews-c">
    <div class="kicker center">CLIENT TESTIMONIALS</div>
    <div class="title center">WHAT OUR CUSTOMER SAYS</div>
    <span class="chev" style="left:11px">‹</span><span class="chev" style="left:287px">›</span>
    <div class="card" style="left:28px"><q>“ Lorem ipsum dolor sit amet, consectetur adipiscing elit, sed do eiusmod tempor incididunt ut labore et dolore magna minim veniam, quis aliqua Ut enim ad minim veniam.</q><div class="who"><i></i><div>Ada Renn<span class="stars">★★★★★</span></div></div></div>
    <div class="card" style="left:157px"><q>“ Lorem ipsum dolor sit amet, consectetur adipiscing elit, sed do eiusmod tempor incididunt ut labore et dolore magna minim veniam, quis aliqua Ut enim ad minim veniam.</q><div class="who"><i></i><div>Lio Marsh<span class="stars">★★★★★</span></div></div></div>
  </section>
  <section class="offer">
    <div class="kicker center">NEW OFFER</div>
    <div class="title center">GET 20% OFFER</div>
    <div class="photo offer-shot" role="img" aria-label="Shortcut cheat-sheet desk mat with keyboard and mouse"></div>
    <div class="clock"><div class="kicker">SALE END IN</div>
      <div class="digits"><div><b>01</b><span>DAYS</span></div><em>:</em><div><b>23</b><span>HOURS</span></div><em>:</em><div><b>39</b><span>MINS</span></div><em>:</em><div><b>46</b><span>SECS</span></div></div></div>
    <p class="copy offer-note">We also sell complete Gridwell Sheets packages for a professional, stylish, clear and efficient spreadsheet for whatever financial tasks you may have! This makes the journey to a more profitable economy easier!</p>
    <div class="offer-btn"><span class="btn">SHOP NOW</span></div>
  </section>
  <footer class="foot foot-c">
    <div class="foot-brand"><b></b>TAMQUIST</div>
    <div class="fcol" style="left:107px"><h4>QUICK LINKS</h4><a>Home</a><a>About Us</a><a>Our Services</a><a>Products</a><a>Contact Us</a></div>
    <div class="fcol" style="left:169px"><h4>HELP LINKS</h4><a>Privacy policy</a><a>Terms of use</a><a>Sitemap</a></div>
    <div class="fcol" style="left:227px"><h4>SOCIAL MEDIA</h4><div class="socials"><i></i><i></i><i></i><i></i><i></i></div></div>
    <div class="rights">Copyright © 2024 Tamquist . All rights reserved.</div>
  </footer>
</main>

</body>
</html>
```